Los Angeles based Demolition, Grading, and Structural concrete Contractor in need of a Sale brochure

We are a Los Angeles-based demolition, grading, and structural concrete contractor looking for a professionally designed sales brochure that represents our company and services. The brochure should be visually appealing, easy to read, and include the following:

-Company Logo: Prominently displayed to enhance brand identity.

-Services We Offer: A clear breakdown of our key services, including demolition, grading, and structural concrete work.

-Project Scope & Capabilities: A brief explanation of the type of projects we handle (residential, commercial, industrial).

-Pricing Information: Mention that demolition services start at $20,000. This price includes complete demolition of structure, safe debris removal and hauling, site preparation for new construction.

-Contact Information: Our phone number(818.502.6617), email(contact@brovanbuildersinc.example) , and website for potential clients to reach out.

The design should reflect the professionalism and strength of our industry, using a modern, clean layout with bold colors that align with construction and demolition themes. Images of past work or stock photos representing our services are encouraged.

Final deliverables should be print-ready (PDF) and digital-friendly formats. Looking forward to creative and impactful designs!

```html
<!DOCTYPE html>
<html lang="en">
<head>
<meta charset="utf-8">
<title>Brovan Builders – Sales Flyer</title>
<link href="https://fonts.googleapis.com/css2?family=Oswald:wght@600;700&family=Arimo:wght@400;700&display=swap" rel="stylesheet">
<style>
  :root{
    --brand-blue:#1f73c0;
    --panel-grey:#86878a;
    --ink:#111111;
    --paper:#ffffff;
    --backdrop:#dcdcdc;
    --head-font:'Oswald', 'Arial Narrow', sans-serif;
    --body-font:'Arimo', Arial, sans-serif;
  }
  *{margin:0;padding:0;box-sizing:border-box}
  html,body{width:714px;height:1200px;overflow:hidden;background:var(--backdrop)}
  .stage{position:relative;width:714px;height:1200px}
  .flyer-frame{position:absolute;left:20px;top:343px;width:674px;height:514px;box-shadow:0 4px 10px rgba(0,0,0,.25)}
  .flyer{position:absolute;left:0;top:0;width:868px;height:662px;background:var(--paper);
    transform:scale(.7765);transform-origin:0 0;color:var(--ink);font-family:var(--body-font)}
  .brand{position:absolute;left:38px;top:34px;width:166px}
  .brand-name{display:flex;align-items:center;gap:8px;font-family:var(--head-font);font-weight:700;
    font-size:27px;line-height:1;color:var(--brand-blue);letter-spacing:.5px}
  .brand-name .mark{width:16px;height:16px;background:var(--brand-blue);flex:none}
  .brand-sub{margin-top:6px;font-family:var(--head-font);font-weight:700;font-size:16px;letter-spacing:5px;color:var(--brand-blue)}
  .brand-tagline{margin-top:22px;font-family:var(--head-font);font-weight:600;font-size:9px;white-space:nowrap}
  .brand-tagline .dot{color:var(--brand-blue)}
  .headline{position:absolute;left:239px;top:26px;font-family:var(--head-font);font-weight:700;font-size:37px;
    line-height:1.1;letter-spacing:-.3px;white-space:nowrap}
  .intro{position:absolute;left:240px;top:78px;width:600px;font-size:12.5px;line-height:15px}
  .service{position:absolute;top:147px;width:256px}
  .service-photo{width:256px;height:264px}
  .service h2{margin-top:12px;font-family:var(--head-font);font-weight:700;font-size:24px;line-height:1.1}
  .service p{margin-top:2px;font-size:13px;line-height:15px}
  .svc-demo{left:40px}.svc-grade{left:306px}.svc-concrete{left:574px}
  .photo-demo{background:linear-gradient(160deg,#b9c2b0 0%,#8c7d55 50%,#6b5a3d 100%)}
  .photo-grade{background:linear-gradient(180deg,#3d7fd6 0%,#9fb4c4 28%,#8d8d8a 45%,#d9c19a 75%,#cdb48c 100%)}
  .photo-concrete{background:linear-gradient(170deg,#7d8a80 0%,#b8b8b4 40%,#c9b493 75%,#a98f6a 100%)}
  .band{position:absolute;top:505px;height:157px;color:#fff}
  .band-blue{left:0;width:562px;background:var(--brand-blue)}
  .band-grey{left:574px;width:294px;background:var(--panel-grey)}
  .band h3{font-family:var(--head-font);font-weight:600;font-size:21px;line-height:1}
  .pricing{position:absolute;left:40px;top:20px;width:240px}
  .pricing .lead{margin-top:14px;font-family:var(--head-font);font-weight:600;font-size:14px}
  .pricing ul{list-style:none;margin-top:5px}
  .pricing li{font-size:12px;font-weight:700;line-height:17.5px;display:flex;align-items:center;gap:7px}
  .pricing li svg{flex:none}
  .scope{position:absolute;left:306px;top:20px;width:252px}
  .scope p{margin-top:14px;font-size:10px;line-height:14px}
  .contact{position:absolute;left:28px;top:20px}
  .contact .phone{margin-top:14px;font-size:17px;letter-spacing:.5px}
  .contact .line{margin-top:6px;font-size:12px;letter-spacing:.3px}
</style>
</head>
<body>
<main class="stage">
  <div class="flyer-frame">
    <article class="flyer">
      <header>
        <div class="brand">
          <div class="brand-name"><span class="mark"></span>BROVAN</div>
          <div class="brand-sub">BUILDERS</div>
          <div class="brand-tagline">Demolition <span class="dot">•</span> Grading <span class="dot">•</span> Structural Concrete</div>
        </div>
        <h1 class="headline">Built for Strength, Engineered for Success</h1>
        <p class="intro">Brovan Builders Inc. is a trusted demolition, grading, and structural concrete contractor serving Los Angeles and beyond. With years of experience in the industry, we bring precision, efficiency, and safety to every project—whether residential, commercial, or industrial.</p>
      </header>

      <section class="service svc-demo">
        <div class="service-photo photo-demo" role="img" aria-label="Yellow excavator clearing a wooded lot during demolition"></div>
        <h2>Demolition</h2>
        <p>Safe, efficient, and complete structure removal, including debris hauling.</p>
      </section>
      <section class="service svc-grade">
        <div class="service-photo photo-grade" role="img" aria-label="Graded building pad beside tall concrete retaining walls under blue sky"></div>
        <h2>Grading</h2>
        <p>Site preparation for new builds, leveling, excavation, and soil stabilization.</p>
      </section>
      <section class="service svc-concrete">
        <div class="service-photo photo-concrete" role="img" aria-label="Aerial view of a hillside structural concrete foundation under construction"></div>
        <h2>Structural Concrete</h2>
        <p>Foundations, retaining walls, slabs, and reinforced concrete work.</p>
      </section>

      <section class="band band-blue">
        <div class="pricing">
          <h3>Transparent Pricing</h3>
          <div class="lead">Demolition services start at $20,000</div>
          <ul>
            <li><svg width="9" height="9" viewBox="0 0 9 9"><path d="M0 0H6L9 4.5 6 9H0Z" fill="#fff"/></svg>Complete structure removal</li>
            <li><svg width="9" height="9" viewBox="0 0 9 9"><path d="M0 0H6L9 4.5 6 9H0Z" fill="#fff"/></svg>Safe debris removal &amp; hauling</li>
            <li><svg width="9" height="9" viewBox="0 0 9 9"><path d="M0 0H6L9 4.5 6 9H0Z" fill="#fff"/></svg>Site preparation for new construction</li>
          </ul>
        </div>
        <div class="scope">
          <h3>Project Scope &amp; Capabilities</h3>
          <p>We handle projects of all sizes, from small-scale residential demolitions to large commercial and industrial site preparations. Our skilled team ensures compliance with local regulations and industry best practices, delivering quality work on time and within budget.</p>
        </div>
      </section>

      <section class="band band-grey">
        <div class="contact">
          <h3>Contact Us</h3>
          <div class="phone">818.502.6617</div>
          <div class="line">contact@brovanbuildersinc.example</div>
          <div class="line">www.brovanbuildersinc.example</div>
        </div>
      </section>
    </article>
  </div>
</main>
</body>
</html>
```